Brindle Sky Port needs a new upscale business card design for our high end aircraft hangar complex

Brindle Sky Port (BSP) is a large, upscale jet hangar complex in the US housing expensive aircraft. We need a new business card design, using our current logo. We will be attending a industry convention and need a card design that will stand out and be remembered by aircraft owners and private pilots.

Target Market(s)

Aircraft pilots or owners looking for a new upscale hangar

Industry/Entity Type

Airport

Contact Information for Business Card

I like to use very heavy card stock, 400#, double sided. Square, no rounded edges please.

Colors
3276b5
0255a3
85abd2

Requirements
Must have
• An expensive, classy design, vivid colors.
Nice to have
• Needs to look very expensive and classy, and have some "pop". Designer must be able to download or copy my current typeface or fonts.
• One card side might be black with the "Logo and Brindle Sky Port Double line image in blue (or try gold, or glossy black), and perhaps have a grayed out "K720 jet silhouette". The other card side would have our contact info, and perhaps the "BSP Logo only". I'd like my contact info 'stacked', not in a paragraph format.
Should not have
• Should not look "too busy". Having a double-sided card will help.

```html
<!DOCTYPE html>
<html lang="en">
<head>
<meta charset="utf-8">
<title>Brindle Sky Port – Business Card</title>
<link rel="stylesheet" href="https://fonts.googleapis.com/css2?family=Russo+One&family=Arimo:wght@400&display=swap">
<style>
  :root {
    --page: #e9e9e9;
    --black: #0b0b0b;
    --charcoal: #262626;
    --charcoal-light: #333333;
    --silver: #d9d9d9;
    --white: #ffffff;
    --ink: #1a1a1a;
    --blue: #0255a3;
    --blue-mid: #3276b5;
  }
  html, body {
    margin: 0;
    width: 1200px;
    height: 1020px;
    overflow: hidden;
    background: var(--page);
  }
  .sheet {
    position: relative;
    width: 1200px;
    height: 1020px;
  }
  .card {
    position: absolute;
    left: 180px;
    width: 840px;
    height: 470px;
    overflow: hidden;
    box-shadow: 0 6px 18px rgba(0,0,0,0.18);
  }
  .card--front {
    top: 30px;
    background:
      linear-gradient(180deg, #2b2b2b 0%, #161616 40%, #000 41%, #0d0d0d 100%);
  }
  .brand {
    position: absolute;
    inset: 0;
    display: flex;
    flex-direction: column;
    align-items: center;
    justify-content: center;
    font-family: "Russo One", sans-serif;
    color: var(--silver);
    text-transform: uppercase;
  }
  .brand__initials {
    font-size: 140px;
    line-height: 1;
    letter-spacing: 6px;
  }
  .brand__name {
    font-size: 40px;
    line-height: 1.15;
    letter-spacing: 2px;
    margin-top: 8px;
    text-align: center;
  }

  .card--back {
    top: 540px;
    background: var(--white);
  }
  .card__band {
    position: absolute;
    inset: 0;
    width: 100%;
    height: 100%;
  }
  .band-mark {
    position: absolute;
    left: 30px;
    top: 182px;
    font-family: "Russo One", sans-serif;
    color: var(--white);
    font-size: 56px;
    letter-spacing: 3px;
  }
  .band-watermark {
    position: absolute;
    left: 10px;
    top: 150px;
    font-family: "Russo One", sans-serif;
    color: rgba(255,255,255,0.05);
    font-size: 150px;
    letter-spacing: 6px;
    line-height: 1;
  }
  .contact {
    position: absolute;
    left: 280px;
    top: 78px;
    font-family: "Arimo", sans-serif;
    color: var(--ink);
  }
  .contact__name {
    font-family: "Russo One", sans-serif;
    font-size: 33px;
    letter-spacing: 1px;
    margin: 0;
    text-transform: uppercase;
    white-space: nowrap;
  }
  .contact__surname { color: var(--blue); }
  .contact__role {
    font-size: 27px;
    margin: 4px 0 0 6px;
  }
  .contact__list {
    list-style: none;
    margin: 62px 0 0 0;
    padding: 0;
    font-size: 27px;
    line-height: 1.45;
  }
  .contact__list li:nth-child(1) { margin-left: 30px; }
  .contact__list li:nth-child(2) { margin-left: 38px; }
  .contact__list li:nth-child(3) { margin-left: 47px; }
  .contact__list li:nth-child(4) { margin-left: 56px; }
  .accent { color: var(--blue); }
</style>
</head>
<body>
<main class="sheet">
  <section class="card card--front" aria-label="Card front">
    <div class="brand">
      <span class="brand__initials">BSP</span>
      <span class="brand__name">Brindle<br>Sky Port</span>
    </div>
  </section>

  <section class="card card--back" aria-label="Card back">
    <svg class="card__band" viewBox="0 0 840 470" preserveAspectRatio="none" aria-hidden="true">
      <polygon points="0,0 212,0 322,470 0,470" fill="#262626"/>
      <polygon points="212,0 222,0 332,470 322,470" fill="#0255a3"/>
    </svg>
    <span class="band-watermark" aria-hidden="true">BSP</span>
    <span class="band-mark">BSP</span>

    <div class="contact">
      <h1 class="contact__name">Daniel R. <span class="contact__surname">Whitcombe</span></h1>
      <p class="contact__role">Logistic director</p>
      <ul class="contact__list">
        <li><span class="accent">+</span>555.014.227.360</li>
        <li>daniel.whitcombe@<span class="accent">brindle</span>skyport.com</li>
        <li><span class="accent">brindle</span>skyport.com</li>
        <li>48 Hangar Row, State, ST 20481</li>
      </ul>
    </div>
  </section>
</main>
</body>
</html>
```